Business Card Design

Online clothing womens clothing store, I sell my clothing online and at the markets.

i would like the attached picture on the front of the card and the contact information on the back.

Industry/Entity Type

Business

Contact Information for Business Card

Marlow Thread
Karen Whitfield
(Instagram symbol) _marlow_thread_
(Facebook symbol) www.fakebookexample.com/marlowthreadau/

W : www.marlowthread.example.au
E : info@marlowthread.example.au
P : 0498716204

```html
<!DOCTYPE html>
<html lang="en">
<head>
<meta charset="utf-8">
<title>Marlow Thread – Business Card</title>
<link rel="stylesheet" href="https://fonts.googleapis.com/css2?family=Josefin+Sans:wght@200;300&family=Open+Sans:wght@400;600;700&display=swap">
<style>
  :root {
    --page: #e4e2df;
    --paper: #f1f2f3;
    --paper-shade: #dfe1e4;
    --cloud-light: #c9c8cf;
    --cloud-dark: #8f8d98;
    --band: #050505;
    --ink: #141414;
    --ink-inverse: #ffffff;
    --sky: #d3d8d8;
    --mist: #9aa7ab;
    --ridge: #4e5c63;
    --shadow: rgba(0,0,0,0.18);
  }
  * { box-sizing: border-box; margin: 0; padding: 0; }
  html, body {
    width: 1200px; height: 858px; overflow: hidden;
    background: var(--page);
  }
  .canvas { position: relative; width: 1200px; height: 858px; }

  .card {
    position: absolute; top: 271px;
    width: 540px; height: 315px;
    overflow: hidden;
    box-shadow: 0 6px 18px var(--shadow);
  }
  .card--contact { left: 40px; }
  .card--front { left: 620px; }

  .card__bg { position: absolute; inset: 0; width: 100%; height: 100%; }

  /* contact side */
  .brand-name {
    position: absolute; left: 40px; top: 50px;
    font-family: "Josefin Sans", sans-serif; font-weight: 200;
    font-size: 34px; letter-spacing: 8px; color: var(--ink);
    white-space: nowrap;
  }
  .person-name {
    position: absolute; left: 40px; top: 140px;
    font-family: "Open Sans", sans-serif; font-weight: 600;
    font-size: 20px; color: var(--ink); white-space: nowrap;
  }
  .divider {
    position: absolute; left: 250px; top: 116px;
    width: 1.5px; height: 74px; background: var(--ink);
  }
  .contact-list {
    position: absolute; left: 264px; top: 118px;
    list-style: none;
    font-family: "Open Sans", sans-serif; font-size: 13px;
    color: var(--ink); line-height: 22px;
  }
  .contact-list li { display: flex; align-items: center; gap: 6px; white-space: nowrap; }
  .icon-box {
    width: 13px; height: 13px; background: var(--ink);
    display: inline-flex; align-items: center; justify-content: center;
    flex: none;
  }
  .icon-box svg { width: 9px; height: 9px; }

  .social-row {
    position: absolute; top: 273px;
    display: flex; align-items: center; gap: 7px;
    font-family: "Open Sans", sans-serif; font-size: 13px;
    color: var(--ink-inverse); white-space: nowrap;
  }
  .social-row--instagram { left: 40px; }
  .social-row--facebook { left: 196px; }
  .social-mark { width: 11px; height: 11px; background: var(--ink-inverse); flex: none; }

  /* front side */
  .front-name {
    position: absolute; left: 38px; top: 196px;
    font-family: "Open Sans", sans-serif; font-weight: 700;
    font-size: 50px; letter-spacing: 2px;
    color: var(--ink-inverse); white-space: nowrap;
  }
</style>
</head>
<body>
<main class="canvas">

  <section class="card card--contact" aria-label="Business card, contact side">
    <svg class="card__bg" viewBox="0 0 540 315" preserveAspectRatio="none" role="img" aria-label="Soft cloudy sky photograph fading in behind the contact details">
      <defs>
        <linearGradient id="paperFade" x1="0" y1="0" x2="1" y2="0">
          <stop offset="0" stop-color="var(--paper)"/>
          <stop offset="0.45" stop-color="var(--paper)"/>
          <stop offset="0.7" stop-color="var(--cloud-light)"/>
          <stop offset="1" stop-color="var(--cloud-dark)"/>
        </linearGradient>
      </defs>
      <rect width="540" height="315" fill="url(#paperFade)"/>
      <rect width="540" height="26" fill="var(--paper-shade)" opacity="0.6"/>
      <path d="M0 248 Q 400 248 540 190 L540 315 L0 315 Z" fill="var(--band)"/>
    </svg>

    <div class="brand-name">MARLOW THREAD</div>
    <div class="person-name">Karen Whitfield</div>
    <div class="divider"></div>
    <ul class="contact-list">
      <li><span class="icon-box"><svg viewBox="0 0 10 10"><path d="M2 1 L4 1 L4.6 3 L3.5 3.8 C4 5 5 6 6.2 6.5 L7 5.4 L9 6 L9 8 C5 8.5 1.5 5 2 1 Z" fill="#fff"/></svg></span>0498716204</li>
      <li><span class="icon-box"><svg viewBox="0 0 10 10"><rect x="1" y="2.5" width="8" height="5.5" fill="none" stroke="#fff" stroke-width="1"/><path d="M1 2.5 L5 6 L9 2.5" fill="none" stroke="#fff" stroke-width="1"/></svg></span>info@marlowthread.example.au</li>
      <li><span class="icon-box"><svg viewBox="0 0 10 10"><circle cx="5" cy="5" r="3.8" fill="none" stroke="#fff" stroke-width="1"/><path d="M1.2 5 H8.8 M5 1.2 C3 3.5 3 6.5 5 8.8 M5 1.2 C7 3.5 7 6.5 5 8.8" fill="none" stroke="#fff" stroke-width="0.8"/></svg></span>www.marlowthread.example.au</li>
    </ul>

    <div class="social-row social-row--instagram"><span class="social-mark"></span>_marlow_thread_</div>
    <div class="social-row social-row--facebook"><span class="social-mark"></span>www.fakebookexample.com/marlowthreadau/</div>
  </section>

  <section class="card card--front" aria-label="Business card, front side">
    <svg class="card__bg" viewBox="0 0 540 315" preserveAspectRatio="none" role="img" aria-label="Misty mountain landscape photograph under a pale cloudy sky">
      <defs>
        <linearGradient id="mountainMist" x1="0" y1="0" x2="0.3" y2="1">
          <stop offset="0" stop-color="var(--sky)"/>
          <stop offset="0.4" stop-color="var(--mist)"/>
          <stop offset="0.75" stop-color="var(--ridge)"/>
          <stop offset="1" stop-color="#6f7880"/>
        </linearGradient>
      </defs>
      <rect width="540" height="315" fill="url(#mountainMist)"/>
    </svg>
    <div class="front-name">MARLOW THREAD</div>
  </section>

</main>
</body>
</html>
```